Web Site Design for a Finance (lending) Company

We are opening a new subsidiary that focuses on lending money in the real estate industry. We need a web site designed to represent the business.

The business is lending money to real estate investors. A typical client/borrower will be looking to borrow money to buy a house, renovate it and then sell it at a profit, all within 12 months or less.

Company name is RTV Finance. Our logo is attached.

Attached is a general outline for the web site. We're working on writing more text for each page but this should give you enough to get started with some ideas.

Competitor web site that I like a lot (as an example): https://dorvaleqcapital.example/. Many of the general items on this site match what we will need (description of loan programs, FAQ)

Target Market(s)

Real estate investors (generally individuals or small companies with just a few people) who are buying homes, renovating them and then selling them at a profit.

Industry/Entity Type

Finance

Coding

Coded - Design and coding required

Number of Pages Required

5+ page

Colors

Designer to choose colors to be used in the design.

Requirements
Must have
• Minimalist design. Clean lines without too much clutter. Some stock photography is ok but the photos should not be distracting. They should almost fade in to the background so that user can focus on the key information about what our company does instead. We are a finance company, not a design company, so the information about our products will be more interesting to site visitors than the art.
• Some minimalist examples from Snapboard:
• https://www.snapboardia.example/explore/minimalist-web-design/
Nice to have
• If you search in zoovle for "hard money lenders" you will find many examples of web sites from our competition. I have provided a link above to competitor web site that I like a lot.
• I have attached our logo in EPS format. Logo is green. Web site doesn't have to be green but it should be of a color that will work well with the logo.

```html
<!DOCTYPE html>
<html lang="en">
<head>
<meta charset="utf-8">
<title>RTV Finance</title>
<link rel="stylesheet" href="https://fonts.googleapis.com/css2?family=Lato:wght@400;700;900&family=Open+Sans:wght@400;600&family=Roboto:wght@400;500&display=swap">
<style>
:root{
  --green:#0b4a2c;
  --green-dark:#083a22;
  --ink:#333333;
  --muted:#555555;
  --paper:#ffffff;
  --mist:#efeeec;
  --stone:#8a8a8a;
  --night:#222222;
  --line:#d9d9d9;
}
*{box-sizing:border-box;margin:0;padding:0}
html,body{width:1200px;height:2970px;overflow:hidden;background:var(--paper)}
body{font-family:"Open Sans",Arial,sans-serif;color:var(--ink);position:relative}
a{color:inherit;text-decoration:none}

.site-header{position:absolute;top:0;left:0;width:1200px;height:104px;background:var(--paper);z-index:3}
.brand{position:absolute;left:100px;top:30px;display:flex;align-items:center;gap:12px;font-family:"Lato",sans-serif;font-weight:700;font-size:26px;color:var(--green)}
.brand-mark{width:22px;height:22px;background:var(--green)}
.main-nav{position:absolute;right:100px;top:0;height:104px;display:flex;font-family:"Roboto",sans-serif;font-weight:500;font-size:15px;color:var(--ink)}
.main-nav a{display:flex;align-items:center;padding:0 22px;height:104px}
.main-nav a.is-active{background:var(--green);color:#fff;padding:0 24px;margin-right:20px}
.main-nav a+a{margin-left:12px}

.hero{position:absolute;top:104px;left:0;width:1200px;height:516px;background:linear-gradient(180deg,#9aa79a 0%,#7d9468 45%,#5f8a2e 75%,#4e7a22 100%)}
.hero-photo{position:absolute;inset:0;background:linear-gradient(90deg,rgba(60,80,40,.35) 0%,rgba(0,0,0,0) 45%,rgba(180,170,140,.35) 70%,rgba(40,40,40,.45) 100%)}
.hero-title{position:absolute;left:100px;top:90px;font-family:"Lato",sans-serif;font-weight:900;font-size:58px;color:#fff;letter-spacing:.5px}
.hero-text{position:absolute;left:100px;top:186px;width:500px;font-size:16px;line-height:28px;color:#fff}
.btn-outline{position:absolute;left:100px;top:276px;width:114px;height:52px;border:2px solid #fff;color:#fff;font-size:15px;display:flex;align-items:center;justify-content:center}
.slider-dots{position:absolute;left:100px;top:372px;display:flex;gap:4px}
.slider-dots span{width:14px;height:14px;border:1.5px solid #fff;border-radius:50%}
.slider-dots span.is-current{background:var(--green)}
.live-chat{position:absolute;right:0;top:224px;width:48px;height:196px;background:var(--paper);display:flex;flex-direction:column;align-items:center;justify-content:center;gap:12px;z-index:4}
.live-chat b{writing-mode:vertical-rl;transform:rotate(180deg);font-family:"Roboto",sans-serif;font-size:15px;letter-spacing:3px;color:#222}
.live-chat i{width:14px;height:14px;border-radius:50%;background:#222}

.features-band{position:absolute;top:620px;left:0;width:1200px;height:265px;background:var(--mist)}
.feature-cards{position:absolute;top:560px;left:100px;width:1000px;display:flex;gap:20px;z-index:2}
.feature-card{width:320px;height:240px;background:var(--paper);border-top:4px solid var(--green);box-shadow:0 6px 12px rgba(0,0,0,.15);text-align:center;padding-top:22px}
.feature-card.is-highlight{background:var(--green);color:#fff}
.feature-card svg{width:52px;height:58px}
.feature-card h3{font-family:"Lato",sans-serif;font-weight:700;font-size:20px;color:var(--green);margin:12px 0 10px}
.feature-card.is-highlight h3{color:#fff}
.feature-card p{font-size:13px;line-height:24px;padding:0 26px}

.welcome{position:absolute;top:885px;left:0;width:1200px;height:470px;text-align:center}
.section-title{font-family:"Lato",sans-serif;font-weight:700;font-size:28px;color:var(--green);letter-spacing:.3px}
.section-rule{width:88px;height:2px;background:var(--green);margin:22px auto 0}
.welcome .section-title{margin-top:66px}
.welcome p{width:1000px;margin:32px auto 0;font-size:12.6px;line-height:24px;color:var(--muted)}
.welcome p+p{margin-top:14px}
.btn-row{display:flex;justify-content:center;gap:12px;margin-top:44px}
.btn{width:100px;height:48px;display:flex;align-items:center;justify-content:center;font-size:13px;color:#fff}
.btn-primary{background:var(--green)}
.btn-secondary{background:var(--stone)}

.lending{position:absolute;top:1355px;left:0;width:1200px;height:428px;background:var(--mist)}
.lending-copy{position:absolute;left:98px;top:52px;width:480px}
.lending-copy h2{font-family:"Lato",sans-serif;font-weight:700;font-size:21px;line-height:30px;color:var(--green)}
.lending-copy ul{list-style:none;margin-top:24px}
.lending-copy li{position:relative;padding-left:26px;font-size:12.4px;line-height:22px;color:var(--muted);margin-bottom:14px;text-align:justify}
.lending-copy li svg{position:absolute;left:0;top:4px;width:14px;height:12px}
.lending-photo{position:absolute;left:600px;top:0;width:600px;height:428px;background:linear-gradient(135deg,#8a6a5c 0%,#b9a89c 40%,#c4c8c4 65%,#7f8a78 100%)}

.testimonials{position:absolute;top:1783px;left:0;width:1200px;height:620px;text-align:center}
.testimonials .section-title{margin-top:82px}
.testimonial-cards{position:absolute;top:263px;left:100px;width:1000px;display:flex;gap:20px}
.testimonial{position:relative;width:320px;height:220px;background:var(--mist);border:3px solid var(--green);padding-top:72px}
.avatar{position:absolute;left:50%;top:-62px;margin-left:-51px;width:102px;height:102px;border-radius:50%;border:4px solid #fff;box-shadow:0 2px 6px rgba(0,0,0,.3);background:linear-gradient(160deg,#d8d3cc,#9c958e)}
.testimonial h4{font-family:"Lato",sans-serif;font-weight:700;font-size:18px;color:var(--green)}
.testimonial p{font-size:12.6px;line-height:22px;color:var(--muted);padding:0 40px;margin-top:14px}
.section-divider{position:absolute;left:100px;top:2362px;width:1000px;height:1px;background:var(--line)}

.partners{position:absolute;top:2410px;left:100px;width:1000px;display:flex;justify-content:space-between}
.partner{width:132px;height:86px;border:1px solid var(--line);display:flex;align-items:center;justify-content:center}
.partner span{width:64px;height:22px;background:#cfcfcf;border-radius:3px}

.site-footer{position:absolute;top:2558px;left:0;width:1200px;height:412px;background:var(--night);color:#fff}
.footer-brand{position:absolute;left:0;top:72px;width:1200px;display:flex;justify-content:center;align-items:center;gap:12px;font-family:"Lato",sans-serif;font-weight:700;font-size:26px}
.footer-brand .brand-mark{background:#fff}
.footer-contact{position:absolute;top:198px;left:0;width:1200px;display:flex;justify-content:center;gap:30px;font-family:"Roboto",sans-serif;font-size:17px}
.footer-contact span{display:flex;align-items:center;gap:12px}
.footer-contact svg{width:32px;height:32px}
.footer-nav{position:absolute;top:268px;left:0;width:1200px;display:flex;justify-content:center;font-family:"Roboto",sans-serif;font-weight:500;font-size:16px}
.footer-nav a{padding:0 26px}
.footer-nav a+a{border-left:2px solid #fff}
.footer-rule{position:absolute;top:324px;left:100px;width:1000px;height:1px;background:#666}
.copyright{position:absolute;top:360px;left:100px;font-family:"Roboto",sans-serif;font-size:13px;font-weight:500}
.social{position:absolute;top:352px;right:90px;display:flex;gap:6px}
.social span{width:32px;height:32px;border:2px solid #fff;border-radius:50%}
</style>
</head>
<body>

<header class="site-header">
  <a class="brand" href="#"><span class="brand-mark"></span>RTV Finance</a>
  <nav class="main-nav">
    <a class="is-active" href="#">HOME</a>
    <a href="#">ABOUT US</a>
    <a href="#">LOANS</a>
    <a href="#">RESOURCES</a>
    <a href="#">CONTACT US</a>
  </nav>
</header>

<section class="hero" role="img" aria-label="Photo of a house on a green lawn with a hand holding banknotes">
  <div class="hero-photo"></div>
  <h1 class="hero-title">RTV FINANCE</h1>
  <p class="hero-text">RTV Finance is a local business with local knowledge and strong industry relationships.</p>
  <a class="btn-outline" href="#">Read More</a>
  <div class="slider-dots"><span class="is-current"></span><span></span><span></span><span></span><span></span></div>
</section>
<aside class="live-chat"><b>LIVE CHAT</b><i></i></aside>

<div class="features-band"></div>
<div class="feature-cards">
  <article class="feature-card">
    <svg viewBox="0 0 52 58" fill="none" stroke="#0b4a2c" stroke-width="3"><path d="M8 26 L26 10 L44 26"/><circle cx="26" cy="30" r="10"/><path d="M4 44 Q14 52 26 52 Q38 52 48 44"/><text x="26" y="35" font-size="14" text-anchor="middle" fill="#0b4a2c" stroke="none" font-family="Lato,sans-serif" font-weight="700">$</text></svg>
    <h3>BORROWERS</h3>
    <p>Nemo enim ipsam voluptatem quia vol up tas sit aspernatur aut odit aut fugit, sed quia consequuntur.</p>
  </article>
  <article class="feature-card is-highlight">
    <svg viewBox="0 0 52 58" fill="none" stroke="#fff" stroke-width="3"><path d="M12 24 L26 12 L40 24 V34 H12 Z"/><rect x="22" y="24" width="8" height="10"/><path d="M4 42 Q14 50 26 50 Q38 50 48 42"/></svg>
    <h3>INVESTORS</h3>
    <p>Nemo enim ipsam voluptatem quia voluptas sit aspernatur aut odit aut fugit, sed quia consequuntur.</p>
  </article>
  <article class="feature-card">
    <svg viewBox="0 0 52 58" fill="none" stroke="#0b4a2c" stroke-width="3"><rect x="14" y="4" width="24" height="48" rx="3"/><path d="M19 26 L26 20 L33 26 V34 H19 Z"/><path d="M18 42 H34"/></svg>
    <h3>RECENT PROJECTS</h3>
    <p>Nemo enim ipsam voluptatem quia vol up tas sit aspernatur aut odit aut fugit, sed quia consequuntur.</p>
  </article>
</div>

<section class="welcome">
  <h2 class="section-title">WELCOME TO RTV FINANCE</h2>
  <div class="section-rule"></div>
  <p>Nemo enim ipsam voluptatem quia voluptas sit aspernatur aut odit aut fugit, sed quia consequuntur magni dolores eos qui ratione voluptatem sequi nesciunt. Neque porro quisquam est, qui dolorem ipsum quia dolor sit amet, consectetur, adipisci velit, sed quia non numquam eius modi tempora incidunt ut labore et dolore magnam aliquam quaerat voluptatem.</p>
  <p>Nam libero tempore, cum soluta nobis est eligendi optio cumque nihil impedit quo minus id quod maxime placeat facere possimus, omnis voluptas assumenda est, omnis dolor repellendus.</p>
  <div class="btn-row"><a class="btn btn-primary" href="#">Read More</a><a class="btn btn-secondary" href="#">Contact Us</a></div>
</section>

<section class="lending">
  <div class="lending-copy">
    <h2>Local real estate experts lending to local real estate investors</h2>
    <ul>
      <li><svg viewBox="0 0 14 12" fill="none" stroke="#555" stroke-width="1.4"><path d="M1 6 H11 M7 2 L11 6 L7 10"/></svg>RTV Finance is a local business with local knowledge and strong industry relationships. A partner with a wide network who offers value added services.</li>
      <li><svg viewBox="0 0 14 12" fill="none" stroke="#555" stroke-width="1.4"><path d="M1 6 H11 M7 2 L11 6 L7 10"/></svg>RTV has an established pool of experienced investors available for your real estate investment needs.</li>
      <li><svg viewBox="0 0 14 12" fill="none" stroke="#555" stroke-width="1.4"><path d="M1 6 H11 M7 2 L11 6 L7 10"/></svg>Loans offered (Fix and Flip, Commercial)</li>
      <li><svg viewBox="0 0 14 12" fill="none" stroke="#555" stroke-width="1.4"><path d="M1 6 H11 M7 2 L11 6 L7 10"/></svg>Why borrow from RTV (experts, fast approval, professional, a partner, selective, competitive rates and fees).</li>
    </ul>
  </div>
  <div class="lending-photo" role="img" aria-label="Photo of hands exchanging banknotes and a house key in front of townhouses"></div>
</section>

<section class="testimonials">
  <h2 class="section-title">WHAT CLIENT SAY</h2>
  <div class="section-rule"></div>
  <div class="testimonial-cards">
    <article class="testimonial"><div class="avatar" role="img" aria-label="Portrait photo of Paul Reed"></div><h4>PAUL REED</h4><p>Nam libero tempore, cum soluta nobis est eligendi optio cumque nihil impedit quo minus id quod.</p></article>
    <article class="testimonial"><div class="avatar" role="img" aria-label="Portrait photo of Nora Bell"></div><h4>NORA BELL</h4><p>Nam libero tempore, cum soluta nobis est eligendi optio cumque nihil impedit quo minus id quod.</p></article>
    <article class="testimonial"><div class="avatar" role="img" aria-label="Portrait photo of Owen Hart"></div><h4>OWEN HART</h4><p>Nam libero tempore, cum soluta nobis est eligendi optio cumque nihil impedit quo minus id quod.</p></article>
  </div>
</section>
<div class="section-divider"></div>

<div class="partners" aria-label="Partners">
  <div class="partner"><span></span></div>
  <div class="partner"><span></span></div>
  <div class="partner"><span></span></div>
  <div class="partner"><span></span></div>
  <div class="partner"><span></span></div>
  <div class="partner"><span></span></div>
</div>

<footer class="site-footer">
  <div class="footer-brand"><span class="brand-mark"></span>RTV Finance</div>
  <div class="footer-contact">
    <span><svg viewBox="0 0 32 32" fill="none" stroke="#fff" stroke-width="2"><circle cx="16" cy="16" r="14"/><rect x="9" y="11" width="14" height="10" fill="#fff" stroke="none"/><path d="M9 11 L16 17 L23 11" stroke="#222" stroke-width="1.5"/></svg>info@rtvfinance.example</span>
    <span><svg viewBox="0 0 32 32" fill="none" stroke="#fff" stroke-width="2"><circle cx="16" cy="16" r="14"/><path d="M11 9 L14 9 L15 13 L13 14.5 Q15 18 17.5 19 L19 17 L23 18 L23 21 Q20 24 15 20 Q10 16 11 9 Z" fill="#fff" stroke="none"/></svg>+180 555 0142</span>
  </div>
  <nav class="footer-nav">
    <a href="#">HOME</a><a href="#">ABOUT US</a><a href="#">LOANS</a><a href="#">RESOURCES</a><a href="#">CONTACT US</a>
  </nav>
  <div class="footer-rule"></div>
  <p class="copyright">Copyrights © 2017 RTV Finance. All Rights Reserved</p>
  <div class="social"><span></span><span></span><span></span><span></span><span></span></div>
</footer>

</body>
</html>
```